Business Card design which attached logo. Company is called Crestline Shield and main colours are Orange & Black.

Company specialises in Paint Protection and Detailing for supercars.

Details needed on business card:

Sales

Address: Unit 14, 517 Hadley Road, Fernvale Heights, NSW 2200

Phone: 02 6194 2738

website: www.crestlineshield.com.au

Email: sales@crestlineshield.com.au

```html
<!DOCTYPE html>
<html lang="en">
<head>
<meta charset="utf-8">
<title>Crestline Shield – Business Card</title>
<link href="https://fonts.googleapis.com/css2?family=Open+Sans:wght@300;400&display=swap" rel="stylesheet">
<style>
  :root {
    --backdrop: #e3e1dc;
    --card: #070707;
    --orange: #e0521c;
    --grey: #b9b9b9;
    --white: #e8e8e8;
  }
  * { box-sizing: border-box; margin: 0; padding: 0; }
  html, body {
    width: 1200px; height: 781px; overflow: hidden;
    background: var(--backdrop);
    font-family: "Open Sans", Arial, sans-serif;
  }
  .stage {
    position: relative; width: 1200px; height: 781px;
    display: flex; align-items: center; justify-content: center; gap: 40px;
  }
  .card {
    position: relative; width: 540px; height: 309px;
    background: var(--card);
    box-shadow: 0 12px 28px rgba(0,0,0,0.28);
  }
  .wordmark {
    font-weight: 300; color: var(--orange);
    letter-spacing: 3px; text-transform: uppercase; white-space: nowrap;
  }
  /* Front */
  .card-front { display: flex; flex-direction: column; align-items: center; justify-content: center; gap: 26px; }
  .card-front .wordmark { font-size: 34px; }
  .front-url { font-size: 14px; color: var(--white); letter-spacing: 0.5px; }
  .front-url .accent { color: var(--orange); }
  /* Back */
  .card-back .wordmark.brand { position: absolute; top: 62px; left: 0; right: 0; text-align: center; font-size: 26px; }
  .back-info {
    position: absolute; top: 150px; left: 0; right: 0;
    display: flex; justify-content: center; align-items: center; gap: 18px;
  }
  .identity { text-align: right; }
  .identity .name { font-size: 20px; font-weight: 400; color: var(--orange); letter-spacing: 0.5px; text-transform: uppercase; }
  .identity .role { font-size: 15px; color: var(--grey); font-weight: 300; margin-top: 2px; }
  .divider { width: 1px; height: 62px; background: var(--orange); }
  .contacts { list-style: none; font-size: 12px; color: var(--white); font-weight: 300; }
  .contacts li { display: flex; align-items: center; gap: 7px; line-height: 19px; }
  .contacts svg { width: 10px; height: 10px; flex: none; }
  .contacts .accent { color: var(--orange); }
  .address {
    position: absolute; top: 240px; left: 0; right: 0; text-align: center;
    font-size: 12.5px; color: var(--grey); font-weight: 300;
  }
</style>
</head>
<body>
<main class="stage">
  <section class="card card-front">
    <div class="wordmark">Crestline Shield</div>
    <p class="front-url">www.<span class="accent">crestlineshield</span>.com.au</p>
  </section>

  <section class="card card-back">
    <div class="wordmark brand">Crestline Shield</div>
    <div class="back-info">
      <div class="identity">
        <div class="name">Crestline Shield</div>
        <div class="role">Founder &amp; CEO</div>
      </div>
      <div class="divider"></div>
      <ul class="contacts">
        <li>
          <svg viewBox="0 0 10 10" aria-hidden="true"><rect x="2.5" y="0.5" width="5" height="9" rx="1" fill="none" stroke="#e0521c" stroke-width="1.2"/></svg>
          02 6194 2738
        </li>
        <li>
          <svg viewBox="0 0 10 10" aria-hidden="true"><rect x="0.6" y="2" width="8.8" height="6" fill="none" stroke="#e0521c" stroke-width="1.1"/><path d="M0.6 2 L5 5.5 L9.4 2" fill="none" stroke="#e0521c" stroke-width="1.1"/></svg>
          sales@crestlineshield.com.au
        </li>
        <li>
          <svg viewBox="0 0 10 10" aria-hidden="true"><circle cx="5" cy="5" r="4.2" fill="none" stroke="#e0521c" stroke-width="1.1"/><path d="M0.8 5 H9.2 M5 0.8 C2.8 3 2.8 7 5 9.2 M5 0.8 C7.2 3 7.2 7 5 9.2" fill="none" stroke="#e0521c" stroke-width="0.9"/></svg>
          www.<span class="accent">crestlineshield</span>.com.au
        </li>
      </ul>
    </div>
    <p class="address">Unit 14, 517 Hadley Road, Fernvale Heights, NSW 2200</p>
  </section>
</main>
</body>
</html>
```